Need Business Card for our Real Estate Business with Sales Executive's Picture

PANTONE 484 C ( RED)

PANTONE 2766 C ( BLUE

Industry/Entity Type

Real Estate

Contact Information for Business Card

Name, Mobile, email, & picture of Person
Agency Phone, address, Web address

Requirements
Must have
• Our Logo Colours, Agent Picture,

```html
<!DOCTYPE html>
<html lang="en">
<head>
<meta charset="utf-8">
<title>Mesa Ridge Realty – Business Card</title>
<link href="https://fonts.googleapis.com/css2?family=Amaranth:wght@700&family=Open+Sans:wght@400;600&display=swap" rel="stylesheet">
<style>
  :root {
    --page-bg: #e6e4e1;
    --card-top: #f7f6f3;
    --card-foot: #eeece8;
    --brand-blue: #1c2a5c;
    --brand-blue-deep: #141b4d;
    --brand-red: #9a3324;
    --text-light: #ffffff;
    --text-soft: #dfe3ee;
    --text-dark: #1d2440;
    --photo-a: #3b4a7a;
    --photo-b: #8a7a6e;
  }
  * { margin: 0; padding: 0; box-sizing: border-box; }
  html, body { width: 1200px; height: 1054px; overflow: hidden; }
  body { background: var(--page-bg); position: relative; font-family: "Open Sans", sans-serif; }

  .card {
    position: absolute; left: 80px; top: 213px;
    width: 1040px; height: 628px;
    background: var(--card-top);
    overflow: hidden;
    box-shadow: 0 14px 40px rgba(0,0,0,0.18);
  }
  .brand {
    position: absolute; right: 78px; top: 88px;
    display: flex; align-items: center; gap: 16px;
  }
  .brand-mark { width: 22px; height: 22px; background: var(--brand-red); }
  .brand-name {
    font-family: "Amaranth", sans-serif; font-weight: 700;
    font-size: 52px; letter-spacing: 1px; color: var(--brand-blue);
  }
  .info-band {
    position: absolute; left: 0; top: 237px; width: 100%; height: 301px;
    background: linear-gradient(90deg, var(--brand-blue-deep), var(--brand-blue) 60%, #243673);
  }
  .accent-rule {
    position: absolute; left: 0; top: 538px; width: 100%; height: 12px;
    background: var(--brand-red);
  }
  .card-foot {
    position: absolute; left: 0; top: 550px; width: 100%; height: 78px;
    background: var(--card-foot);
    display: flex; align-items: center; justify-content: center;
  }
  .address { font-size: 25px; color: var(--text-dark); }
  .agent-photo {
    position: absolute; left: 0; top: 93px; width: 389px; height: 445px;
    background: linear-gradient(180deg, var(--photo-b) 0%, var(--photo-b) 35%, var(--photo-a) 60%, var(--brand-blue-deep) 100%);
  }
  .agent {
    position: absolute; left: 483px; top: 270px;
  }
  .agent-name {
    font-family: "Amaranth", sans-serif; font-weight: 700;
    font-size: 37px; color: var(--text-light); line-height: 1.1;
  }
  .agent-title { font-size: 26px; color: var(--text-soft); margin-top: 4px; }
  .contacts { list-style: none; margin-top: 30px; }
  .contacts li {
    display: flex; align-items: center; gap: 16px;
    font-size: 26px; color: var(--text-soft); height: 35.5px;
  }
  .contacts svg { width: 20px; height: 20px; flex: none; fill: var(--brand-red); }
</style>
</head>
<body>
  <div class="card">
    <div class="brand">
      <span class="brand-mark"></span>
      <span class="brand-name">Mesa Ridge Realty</span>
    </div>

    <div class="info-band"></div>
    <div class="agent-photo" role="img" aria-label="Portrait photo of the agent in a navy suit"></div>

    <div class="agent">
      <div class="agent-name">Diane Holloway</div>
      <div class="agent-title">Managing Director</div>
      <ul class="contacts">
        <li>
          <svg viewBox="0 0 20 20" aria-hidden="true"><path d="M5 1h10a1 1 0 0 1 1 1v16a1 1 0 0 1-1 1H5a1 1 0 0 1-1-1V2a1 1 0 0 1 1-1zm1 2v12h8V3zm4 13a1 1 0 1 0 0 2 1 1 0 0 0 0-2z"/></svg>
          555.204.3187
        </li>
        <li>
          <svg viewBox="0 0 20 20" aria-hidden="true"><path d="M2 7c0-3 3-4 8-4s8 1 8 4v1h-4V6H6v2H2zm3 2h10l2 8H3zm5 2a2.5 2.5 0 1 0 0 5 2.5 2.5 0 0 0 0-5z"/></svg>
          555-619-4420
        </li>
        <li>
          <svg viewBox="0 0 20 20" aria-hidden="true"><path d="M1 4h18v12H1zm2 2v.4l7 4.6 7-4.6V6zm0 2.8V14h14V8.8l-7 4.6z"/></svg>
          dholloway@mesaridgerealty.com
        </li>
        <li>
          <svg viewBox="0 0 20 20" aria-hidden="true"><path d="M10 1a9 9 0 1 0 0 18 9 9 0 0 0 0-18zm0 2c.9 1 1.6 2.6 1.9 4.5H8.1C8.4 5.6 9.1 4 10 3zM3.3 9h3.1a15 15 0 0 0 0 2H3.3a7 7 0 0 1 0-2zm4.7 0h4a13 13 0 0 1 0 2H8a13 13 0 0 1 0-2zm5.6 0h3.1a7 7 0 0 1 0 2h-3.1a15 15 0 0 0 0-2zM8.1 12.5h3.8c-.3 1.9-1 3.5-1.9 4.5-.9-1-1.6-2.6-1.9-4.5z"/></svg>
          www.mesaridgerealty.com
        </li>
      </ul>
    </div>

    <div class="accent-rule"></div>
    <div class="card-foot">
      <p class="address">418 Alder Crest Ave #210, Fairview, CO 80412</p>
    </div>
  </div>
</body>
</html>
```